Boutique Health and Fitness Personal Training Studio

I would like to have a brochure designed which provides a detailed description of the services offered in my business.
I have personal training studio, We look after people from early 20's to 90's, healthy to very unhealthy.
We conduct:
A consultation
An assessment
A personalised program
Personalised training sessions
I would like to base the design around the colours of my logo (attached) and use some of (or all of) the images and information I have also attached.
I would be happy with your own images included also.

Target Market(s)

20 to 90 year olds

Industry/Entity Type

Business

Font styles to use
Serif
Sans Serif

Colors
9bcb3c
add136
cadf82
eaf2ce

Requirements
Must have
• Colour and images of fitness.
• 8.5x14 legal
• Tri fold
• 2 folds with 3 faces back n front
Nice to have
• The feeling of wellbeing
Should not have
• This is not a gym.
• It should have the feel of a private relaxed environment

```html
<!DOCTYPE html>
<html lang="en">
<head>
<meta charset="utf-8">
<title>Evergreen Wellness Studio – Tri-fold Brochure</title>
<link href="https://fonts.googleapis.com/css2?family=Oswald:wght@500;700&family=Open+Sans:wght@400;600;700&display=swap" rel="stylesheet">
<style>
  :root {
    --green-dark: #557f24;
    --green-mid: #6b9a2c;
    --green-bright: #8fbf3c;
    --green-pale: #cadf82;
    --green-mist: #eaf2ce;
    --ink: #2b2b2b;
    --ink-soft: #444;
    --white: #ffffff;
    --pill: #2e3a1f;
    --backdrop: #e9e7e2;
  }
  * { margin: 0; padding: 0; box-sizing: border-box; }
  html, body { width: 907px; height: 1200px; overflow: hidden; background: var(--backdrop); }
  .canvas { position: relative; width: 907px; height: 1200px; overflow: hidden; font-family: "Open Sans", Arial, sans-serif; }
  .sheet { position: absolute; left: 76px; width: 753px; height: 457px; box-shadow: 0 3px 10px rgba(0,0,0,.25); overflow: hidden; }
  .sheet--outside { top: 133px; }
  .sheet--inside { top: 636px; }
  .sheet svg { position: absolute; inset: 0; }
  .block { position: absolute; }
  .heading { font-weight: 700; }
  .copy { font-size: 9.2px; line-height: 11.6px; }
  .on-green { color: var(--white); }
  .on-green .copy { color: #f1f6e4; }

  /* outside */
  .sessions { left: 29px; top: 33px; width: 210px; }
  .sessions .heading { font-size: 12.5px; margin-bottom: 3px; }
  .sessions .copy { font-size: 8.3px; line-height: 10.6px; }
  .cost { left: 29px; top: 122px; width: 215px; }
  .cost .heading { font-size: 12.5px; margin-bottom: 8px; }
  .cost .line { font-size: 11px; margin-bottom: 10px; }
  .cost .heading.second { margin-bottom: 5px; }
  .parking { left: 28px; top: 214px; width: 202px; height: 22px; background: var(--pill); border-radius: 3px; color: var(--green-pale); font-family: "Oswald", sans-serif; font-weight: 500; font-size: 13.5px; line-height: 22px; text-align: center; box-shadow: 0 2px 3px rgba(0,0,0,.35); }

  .contact { left: 251px; top: 72px; width: 251px; text-align: center; color: var(--ink); }
  .brand { font-family: "Open Sans", sans-serif; font-weight: 700; color: var(--green-mid); display: inline-flex; align-items: center; gap: 5px; white-space: nowrap; }
  .brand-dot { width: 9px; height: 9px; border-radius: 50%; background: var(--green-mid); display: inline-block; }
  .contact .brand { font-size: 15px; margin-bottom: 16px; }
  .contact .unit { font-weight: 700; font-size: 13px; line-height: 17px; }
  .contact .street { font-size: 9.5px; margin-top: 5px; }
  .contact .call { font-weight: 700; font-size: 12px; margin-top: 2px; }
  .contact .call span { font-weight: 400; font-size: 9.5px; }
  .contact .visit { font-weight: 700; font-size: 12px; margin-top: 2px; }
  .contact .web { font-weight: 700; font-size: 8.5px; }

  .cover { left: 534px; top: 327px; width: 212px; text-align: center; }
  .cover .tagline { font-family: "Oswald", sans-serif; font-weight: 700; font-size: 20px; color: var(--green-mid); line-height: 26px; }
  .cover .subline { font-family: "Oswald", sans-serif; font-weight: 500; font-size: 16px; color: var(--ink); line-height: 24px; margin-top: 2px; }
  .cover .brand { font-size: 14px; margin-top: 14px; }

  /* inside */
  .allfor { left: 28px; top: 262px; width: 210px; color: var(--ink-soft); }
  .allfor .title { font-family: "Oswald", sans-serif; font-weight: 700; font-size: 15px; color: var(--green-dark); line-height: 19px; }
  .allfor .title.dark { color: var(--ink); margin-top: -1px; }
  .allfor .copy { margin: 4px 0 4px; font-size: 8.6px; line-height: 10.6px; }
  .inside-brand { left: 0; top: 400px; width: 251px; text-align: center; }
  .inside-brand .brand { font-size: 14px; }
  .footer-band { position: absolute; left: 0; bottom: 0; width: 251px; height: 14px; background: #333; }

  .steps { left: 275px; top: 30px; width: 210px; }
  .steps .heading, .program .heading { font-size: 11.5px; margin: 0 0 4px; }
  .steps .copy, .program .copy { font-size: 8.4px; line-height: 10.8px; margin-bottom: 10px; }
  .program { left: 521px; top: 30px; width: 210px; }
  .program .copy { margin-bottom: 22px; }
</style>
</head>
<body>
<div class="canvas">

  <section class="sheet sheet--outside">
    <svg width="753" height="457" viewBox="0 0 753 457">
      <defs>
        <linearGradient id="mid-fade" x1="0" y1="0" x2="1" y2="0">
          <stop offset="0" stop-color="#dcdcdc"/>
          <stop offset=".3" stop-color="#fafafa"/>
          <stop offset="1" stop-color="#e2e2e2"/>
        </linearGradient>
        <linearGradient id="photo-still" x1="0" y1="0" x2="0" y2="1">
          <stop offset="0" stop-color="#e9e9e9"/>
          <stop offset=".5" stop-color="#b9bdb3"/>
          <stop offset="1" stop-color="#7c6a4c"/>
        </linearGradient>
        <linearGradient id="photo-stretch" x1="0" y1="0" x2="1" y2="1">
          <stop offset="0" stop-color="#d9d2cb"/>
          <stop offset=".5" stop-color="#b84a45"/>
          <stop offset="1" stop-color="#3a3b3e"/>
        </linearGradient>
        <linearGradient id="photo-cable" x1="0" y1="0" x2="1" y2="1">
          <stop offset="0" stop-color="#3f4a44"/>
          <stop offset=".55" stop-color="#9a7a62"/>
          <stop offset="1" stop-color="#1f2a2c"/>
        </linearGradient>
      </defs>

      <rect class="panel-left" x="0" y="0" width="251" height="457" fill="var(--green-dark)"/>
      <rect class="panel-middle" x="251" y="0" width="251" height="457" fill="url(#mid-fade)"/>
      <rect class="panel-right" x="502" y="0" width="251" height="457" fill="var(--white)"/>

      <path role="img" aria-label="Photo: trainer stretching a client's shoulder in the studio"
            d="M0,262 Q150,235 240,330 L251,457 L0,457 Z" fill="url(#photo-stretch)"/>
      <path d="M0,256 Q155,226 246,328" fill="none" stroke="var(--white)" stroke-width="6"/>
      <path d="M0,250 Q160,218 251,322" fill="none" stroke="var(--green-bright)" stroke-width="5"/>

      <rect role="img" aria-label="Photo: fresh vegetables, dumbbell, water bottle and tape measure on a table"
            x="251" y="225" width="251" height="232" fill="url(#photo-still)" opacity=".9"/>

      <path role="img" aria-label="Photo: man working out on a cable machine"
            d="M512,0 L753,0 L753,220 Q690,240 620,235 Q530,215 508,120 Q502,60 512,0 Z" fill="url(#photo-cable)"/>
      <path d="M508,0 Q496,150 610,228 Q690,252 753,226" fill="none" stroke="var(--green-dark)" stroke-width="7"/>
      <path d="M500,0 Q488,160 606,236 Q690,262 753,236" fill="none" stroke="var(--green-bright)" stroke-width="4"/>

      <path class="cover-arc" d="M462,457 Q482,282 753,242 L753,466 Z" fill="var(--green-dark)"/>
      <path class="cover-arc" d="M472,457 Q492,290 753,252 L753,466 Z" fill="var(--white)"/>
    </svg>

    <div class="block sessions on-green">
      <h2 class="heading">Your sessions</h2>
      <p class="copy">Training at the studio is professional and caring, but focused and challenging. Typically each session will take approximately 60 minutes. Training times can be organized to suit your needs with early mornings and evenings available.</p>
    </div>
    <div class="block cost on-green">
      <h2 class="heading">The Cost</h2>
      <p class="line">$45 paid in blocks of 5 or 10 sessions</p>
      <h2 class="heading second">Health fund claimable</h2>
      <p class="line">Open 7 days</p>
    </div>
    <div class="block parking">Ample private parking available</div>

    <div class="block contact">
      <div class="brand"><span class="brand-dot"></span>Evergreen Wellness Studio</div>
      <p class="unit">Unit 12<br>Level 2</p>
      <p class="street">48 Wattle Grove Road Fernvale</p>
      <p class="call">call-<span>0400 555 127</span></p>
      <p class="visit">visit us</p>
      <p class="web">www.evergreenwellness.com.au</p>
    </div>

    <div class="block cover">
      <h1 class="tagline">PERSONALISED CARE</h1>
      <p class="subline">IN FITNESS AND HEALTH</p>
      <div class="brand"><span class="brand-dot"></span>Evergreen Wellness Studio</div>
    </div>
  </section>

  <section class="sheet sheet--inside">
    <svg width="753" height="457" viewBox="0 0 753 457">
      <defs>
        <linearGradient id="soft-grey" x1="0" y1="0" x2="1" y2="0">
          <stop offset="0" stop-color="#ececec"/>
          <stop offset="1" stop-color="#fafafa"/>
        </linearGradient>
        <linearGradient id="photo-cross" x1="0" y1="0" x2="1" y2="1">
          <stop offset="0" stop-color="#f1f1f1"/>
          <stop offset=".5" stop-color="#c9b8a6"/>
          <stop offset="1" stop-color="#7d9cad"/>
        </linearGradient>
        <linearGradient id="photo-yoga" x1="0" y1="0" x2="0" y2="1">
          <stop offset="0" stop-color="#6b9a2c"/>
          <stop offset=".5" stop-color="#e39ab8"/>
          <stop offset="1" stop-color="#2f2f2f"/>
        </linearGradient>
        <linearGradient id="photo-lunge" x1="0" y1="0" x2="1" y2="0">
          <stop offset="0" stop-color="#f7f7f7"/>
          <stop offset=".5" stop-color="#3a3a3a"/>
          <stop offset="1" stop-color="#e9e9e9"/>
        </linearGradient>
      </defs>

      <rect class="panel-left" x="0" y="0" width="251" height="457" fill="url(#soft-grey)"/>
      <rect class="panel-middle" x="251" y="0" width="251" height="457" fill="var(--green-dark)"/>
      <rect class="panel-right" x="502" y="0" width="251" height="457" fill="var(--green-dark)"/>

      <path role="img" aria-label="Photo: woman exercising on a cross trainer"
            d="M0,0 L238,0 Q262,150 180,205 Q110,228 30,206 L0,198 Z" fill="url(#photo-cross)"/>
      <path d="M238,0 Q264,152 180,208 Q110,232 0,202" fill="none" stroke="var(--white)" stroke-width="5"/>
      <path d="M246,0 Q274,160 184,216 Q110,242 0,212" fill="none" stroke="var(--green-mid)" stroke-width="6"/>

      <rect role="img" aria-label="Photo: smiling woman seated cross-legged holding a dumbbell and a plate of vegetables"
            x="300" y="308" width="150" height="146" rx="6" fill="url(#photo-yoga)" opacity=".85"/>

      <path role="img" aria-label="Photo: trainer and client doing a lunge exercise together"
            d="M512,457 Q528,300 660,260 Q712,247 753,250 L753,457 Z" fill="url(#photo-lunge)"/>
      <path d="M504,457 Q520,292 656,252 Q712,238 753,240" fill="none" stroke="var(--white)" stroke-width="5"/>
      <path d="M496,457 Q512,282 652,243 Q712,228 753,230" fill="none" stroke="var(--green-bright)" stroke-width="4"/>
    </svg>

    <div class="block allfor">
      <h2 class="title">Health and fitness for all</h2>
      <p class="copy">Exercise programs for all levels of health and fitness and all age groups. Experience in managing a wide range of chronic health conditions.</p>
      <h2 class="title">Experienced professionals</h2>
      <h2 class="title dark">caring for your wellbeing</h2>
      <p class="copy">Exercise Physiologist with over 25 years of experience managing the health and fitness needs of the community.</p>
    </div>
    <div class="block inside-brand"><div class="brand"><span class="brand-dot"></span>Evergreen Wellness Studio</div></div>
    <div class="footer-band"></div>

    <div class="block steps on-green">
      <h2 class="heading">What to Expect</h2>
      <p class="copy">On arrival at the studio you will be asked to complete a questionnaire, which will provide us with information regarding your background with health and fitness, as well as your goals and objectives. Please bring any relevant medical information from medical practitioners or health professionals that you feel may impact on your program.</p>
      <h2 class="heading">Consultation</h2>
      <p class="copy">A consultation will allow you to share your thoughts, concerns and objectives, as well as provide you with ample opportunity to expand on the answers from your questionnaire relating to your prior and current health, medical and physical concerns.</p>
      <h2 class="heading">Assessment</h2>
      <p class="copy">An assessment will be conducted to provide us both with a baseline measure of your cardiovascular fitness, strength, flexibility, balance and body composition measures. These measures provide us with a reference for program design and also to indicate improvements along the way.</p>
    </div>

    <div class="block program on-green">
      <h2 class="heading">The program</h2>
      <p class="copy">Your program will be designed with consideration to your health and fitness background, you objectives and your strengths and weaknesses. It will be personally tailored to your needs and provide you with a plan to focus your energies on.</p>
      <h2 class="heading">Nutrition</h2>
      <p class="copy">Nutrition is central to an effective program, as it will provide you with maximal energy for exercise as well as keeping yourself lean and healthy for a long term fitter lifestyle. Evergreen Wellness Studio provides initial monitoring and ongoing modification in accordance with your needs.</p>
    </div>
  </section>

</div>
</body>
</html>
```